UI/ UX Design for ERP Software

We need a new UX/UI interface for a ERP software for property managers. Our CMMS / ERP solution is made based on responsive design technologies and is coded in PHP.
The overall UX to be similar to Tev Ulna - easy navigation, intuitive menus.

Industry/Entity Type

Property Management

Number of Pages Required

5+ page

Requirements
Must have
• Round dock buttons
Consistent icons across the application
Enough Spacing between buttons/icons/ menu
Consistent Font
Nice to have
• We would like the UX to allow the users to use the application without /minimum training.
Should not have
• we don't want anything that is classic with respect to UX

```html
<!DOCTYPE html>
<html lang="en">
<head>
<meta charset="utf-8">
<title>Property Manager – Properties</title>
<link rel="stylesheet" href="https://fonts.googleapis.com/css2?family=Inter:wght@400;500;600;700&display=swap">
<style>
:root{
  --page:#f2f6fa;
  --card:#ffffff;
  --ink:#171b26;
  --muted:#6b7384;
  --chip:#e6eaf3;
  --dark:#1b1f2b;
  --accent:#0db4f4;
  --option:#f1f7fd;
  --map:#e4e5e7;
}
*{box-sizing:border-box;margin:0;padding:0}
html,body{width:1200px;height:1200px;overflow:hidden}
body{background:var(--page);font-family:"Inter",sans-serif;color:var(--ink);position:relative}
.screen{position:absolute;left:207px;width:785px;background:var(--card);border-radius:22px;overflow:hidden;box-shadow:0 4px 24px rgba(30,50,90,.05)}
.screen--list{top:32px;height:481px}
.screen--detail{top:535px;height:613px}

.round-btn{position:absolute;width:25px;height:25px;border-radius:50%;background:var(--chip);display:flex;align-items:center;justify-content:center}
.round-btn svg{width:12px;height:12px;stroke:var(--ink);fill:none;stroke-width:2;stroke-linecap:round;stroke-linejoin:round}
.round-btn--refresh{left:26px;top:16px;background:#fff;box-shadow:0 1px 6px rgba(0,0,0,.12)}
.round-btn--dark{background:var(--dark)}
.round-btn--dark svg{stroke:#fff;fill:#fff}
.dock-1{left:622px;top:16px}.dock-2{left:660px;top:16px}.dock-3{left:698px;top:16px}.dock-4{left:737px;top:16px}

.breadcrumb{position:absolute;left:58px;top:22px;font-size:9.5px;display:flex;gap:5px;align-items:center}
.breadcrumb b{font-weight:600}
.breadcrumb svg{width:10px;height:10px;stroke:var(--ink);fill:none;stroke-width:2}
.page-title{position:absolute;left:30px;top:52px;font-size:13px;font-weight:700;display:flex;align-items:center;gap:16px}
.page-title svg{width:12px;height:12px;stroke:var(--ink);fill:none;stroke-width:2.5;stroke-linecap:round}

.sort-btn{position:absolute;left:657px;top:79px;width:102px;height:23px;background:var(--chip);border-radius:4px;font-size:8px;font-weight:600;display:flex;align-items:center;justify-content:center;gap:8px}
.sort-btn svg{width:11px;height:11px;stroke:var(--ink);fill:none;stroke-width:2;stroke-linecap:round}

.property-grid{position:absolute;left:32px;top:115px;width:728px;display:grid;grid-template-columns:repeat(4,173px);column-gap:12px;row-gap:33px}
.property-photo{height:112px;border-radius:8px}
.property-name{font-size:8px;font-weight:600;margin:14px 0 0 2px}
.property-address{font-size:7px;font-weight:500;color:var(--muted);margin:5px 0 0 2px;display:flex;align-items:center;gap:4px}
.property-address svg{width:8px;height:8px;stroke:var(--ink);fill:none;stroke-width:2}

.tone-night{background:linear-gradient(160deg,#1c3a86,#22315a 55%,#5a3a26)}
.tone-condo{background:linear-gradient(170deg,#cfd6df,#8794a6 60%,#6c7a54)}
.tone-bedroom{background:linear-gradient(170deg,#6f7482,#d9d6cf 55%,#8c7a50)}
.tone-kitchen{background:linear-gradient(160deg,#d8cbbd,#8a5a3e 55%,#3c2b24)}
.tone-house{background:linear-gradient(180deg,#cfdbe6 0,#dde3e6 35%,#6f7a46 55%,#5c8e2e)}
.tone-pool{background:linear-gradient(180deg,#6fa5dc,#d7dde3 45%,#2d7fd8 75%,#c9c4bb)}
.tone-living{background:linear-gradient(160deg,#b8b5ad,#efeae2 50%,#a78b5d)}
.tone-dusk{background:linear-gradient(180deg,#7f8cc6,#b9bfd0 45%,#2fa4e8 75%,#7d8090)}

.gallery-photo{position:absolute;top:85px;height:146px;border-radius:8px}
.gallery-photo--a{left:0;width:215px;border-radius:0 8px 8px 0}
.gallery-photo--b{left:225px;width:274px}

.section-title{position:absolute;font-size:10px;font-weight:700}
.edit-link{position:absolute;right:302px;top:256px;font-size:8px;font-weight:600;text-decoration:underline;display:flex;gap:5px;align-items:center}
.edit-link svg{width:9px;height:9px;stroke:var(--accent);fill:none;stroke-width:2}

.info-grid{position:absolute;left:26px;top:283px;width:460px;display:grid;grid-template-columns:165px 155px 140px;grid-auto-flow:column;grid-template-rows:repeat(11,28.75px)}
.info-item dt{font-size:7px;color:var(--muted);font-weight:500}
.info-item dd{font-size:7.5px;font-weight:600;margin-top:3px}

.options{position:absolute;left:500px;top:105px;display:grid;grid-template-columns:127px 127px;column-gap:8px;row-gap:7px}
.option{height:31px;border-radius:5px;background:var(--option);font-size:7.5px;font-weight:600;display:flex;align-items:center;gap:12px;padding-left:12px}
.option svg{width:12px;height:12px;stroke:var(--ink);fill:none;stroke-width:1.6;stroke-linejoin:round}
.option--active{background:var(--accent);color:#fff}
.option--active svg{stroke:#fff}

.map{position:absolute;left:500px;top:325px;width:262px;height:265px;border-radius:10px;background:linear-gradient(135deg,#d5d6d8,var(--map) 40%,#ececec);overflow:hidden}
.map-pin{position:absolute;left:136px;top:78px;width:18px;height:18px;border-radius:50%;background:rgba(13,150,220,.3);display:flex;align-items:center;justify-content:center}
.map-pin::after{content:"";width:10px;height:10px;border-radius:50%;background:#1a86c7}
.map-popup{position:absolute;left:125px;top:122px;width:116px;height:67px;background:#fff;border-radius:6px;padding:12px 10px;box-shadow:0 2px 8px rgba(0,0,0,.1)}
.map-popup h4{font-size:8px;font-weight:600}
.map-popup p{font-size:7px;font-weight:500;margin-top:6px;display:flex;gap:4px;line-height:1.35}
.map-popup svg{flex:none;width:8px;height:8px;stroke:var(--ink);fill:none;stroke-width:2;margin-top:1px}
.map-zoom{position:absolute;left:11px;top:209px;width:20px;height:46px;background:#fff;border-radius:4px;font-size:10px;display:flex;flex-direction:column;align-items:center;justify-content:space-around}
</style>
</head>
<body>

<section class="screen screen--list">
  <div class="round-btn round-btn--refresh"><svg viewBox="0 0 24 24"><path d="M20 12a8 8 0 1 1-3-6.2"/><path d="M20 4v5h-5"/></svg></div>
  <nav class="breadcrumb"><svg viewBox="0 0 24 24"><path d="M3 11l9-7 9 7v9h-6v-6H9v6H3z"/></svg><b>Home</b><span>/</span><span>Properties</span></nav>
  <div class="round-btn round-btn--dark dock-1"><svg viewBox="0 0 24 24"><path d="M20 14A8 8 0 1 1 10 4a6 6 0 0 0 10 10z"/></svg></div>
  <div class="round-btn dock-2"><svg viewBox="0 0 24 24"><path d="M4 6h16M4 12h11M4 18h7"/></svg></div>
  <div class="round-btn dock-3"><svg viewBox="0 0 24 24"><path d="M4 9V4h5M20 9V4h-5M4 15v5h5M20 15v5h-5"/></svg></div>
  <div class="round-btn dock-4"><svg viewBox="0 0 24 24"><path d="M14 4h5v16h-5M4 12h11M10 7l5 5-5 5"/></svg></div>

  <h1 class="page-title"><svg viewBox="0 0 24 24"><path d="M15 4l-8 8 8 8"/></svg>Property list</h1>
  <div class="sort-btn"><svg viewBox="0 0 24 24"><path d="M4 6h9M4 12h7M4 18h5M18 5v14M15 16l3 3 3-3"/></svg>Sort by</div>

  <div class="property-grid">
    <article><div class="property-photo tone-night" role="img" aria-label="Office towers lit at night"></div><h3 class="property-name">Prime tower</h3><p class="property-address"><svg viewBox="0 0 24 24"><path d="M12 21s7-7 7-12a7 7 0 0 0-14 0c0 5 7 12 7 12z"/><circle cx="12" cy="9" r="2.5"/></svg>240 Harbourline Street, Vancouver, BC</p></article>
    <article><div class="property-photo tone-condo" role="img" aria-label="Modern white condominium building"></div><h3 class="property-name">Prime tower</h3><p class="property-address"><svg viewBox="0 0 24 24"><path d="M12 21s7-7 7-12a7 7 0 0 0-14 0c0 5 7 12 7 12z"/><circle cx="12" cy="9" r="2.5"/></svg>240 Harbourline Street, Vancouver, BC</p></article>
    <article><div class="property-photo tone-bedroom" role="img" aria-label="Bright bedroom interior"></div><h3 class="property-name">Prime tower</h3><p class="property-address"><svg viewBox="0 0 24 24"><path d="M12 21s7-7 7-12a7 7 0 0 0-14 0c0 5 7 12 7 12z"/><circle cx="12" cy="9" r="2.5"/></svg>240 Harbourline Street, Vancouver, BC</p></article>
    <article><div class="property-photo tone-kitchen" role="img" aria-label="Apartment kitchen and living area"></div><h3 class="property-name">Prime tower</h3><p class="property-address"><svg viewBox="0 0 24 24"><path d="M12 21s7-7 7-12a7 7 0 0 0-14 0c0 5 7 12 7 12z"/><circle cx="12" cy="9" r="2.5"/></svg>240 Harbourline Street, Vancouver, BC</p></article>
    <article><div class="property-photo tone-house" role="img" aria-label="Clubhouse with lawn and garden path"></div><h3 class="property-name">Prime tower</h3><p class="property-address"><svg viewBox="0 0 24 24"><path d="M12 21s7-7 7-12a7 7 0 0 0-14 0c0 5 7 12 7 12z"/><circle cx="12" cy="9" r="2.5"/></svg>240 Harbourline Street, Vancouver, BC</p></article>
    <article><div class="property-photo tone-pool" role="img" aria-label="Apartment block with outdoor pool"></div><h3 class="property-name">Prime tower</h3><p class="property-address"><svg viewBox="0 0 24 24"><path d="M12 21s7-7 7-12a7 7 0 0 0-14 0c0 5 7 12 7 12z"/><circle cx="12" cy="9" r="2.5"/></svg>240 Harbourline Street, Vancouver, BC</p></article>
    <article><div class="property-photo tone-living" role="img" aria-label="Furnished living room"></div><h3 class="property-name">Prime tower</h3><p class="property-address"><svg viewBox="0 0 24 24"><path d="M12 21s7-7 7-12a7 7 0 0 0-14 0c0 5 7 12 7 12z"/><circle cx="12" cy="9" r="2.5"/></svg>240 Harbourline Street, Vancouver, BC</p></article>
    <article><div class="property-photo tone-dusk" role="img" aria-label="Residential complex with pool at dusk"></div><h3 class="property-name">Prime tower</h3><p class="property-address"><svg viewBox="0 0 24 24"><path d="M12 21s7-7 7-12a7 7 0 0 0-14 0c0 5 7 12 7 12z"/><circle cx="12" cy="9" r="2.5"/></svg>240 Harbourline Street, Vancouver, BC</p></article>
  </div>
</section>

<section class="screen screen--detail">
  <div class="round-btn round-btn--refresh"><svg viewBox="0 0 24 24"><path d="M20 12a8 8 0 1 1-3-6.2"/><path d="M20 4v5h-5"/></svg></div>
  <nav class="breadcrumb"><svg viewBox="0 0 24 24"><path d="M3 11l9-7 9 7v9h-6v-6H9v6H3z"/></svg><b>Home</b><span>/</span><b>Properties</b><span>/</span><span>Property detail</span></nav>
  <div class="round-btn round-btn--dark dock-1"><svg viewBox="0 0 24 24"><path d="M20 14A8 8 0 1 1 10 4a6 6 0 0 0 10 10z"/></svg></div>
  <div class="round-btn dock-2"><svg viewBox="0 0 24 24"><path d="M4 6h16M4 12h11M4 18h7"/></svg></div>
  <div class="round-btn dock-3"><svg viewBox="0 0 24 24"><path d="M4 9V4h5M20 9V4h-5M4 15v5h5M20 15v5h-5"/></svg></div>
  <div class="round-btn dock-4"><svg viewBox="0 0 24 24"><path d="M14 4h5v16h-5M4 12h11M10 7l5 5-5 5"/></svg></div>

  <h1 class="page-title"><svg viewBox="0 0 24 24"><path d="M15 4l-8 8 8 8"/></svg>Prime Tower</h1>

  <div class="gallery-photo gallery-photo--a tone-night" role="img" aria-label="Prime Tower exterior at night"></div>
  <div class="gallery-photo gallery-photo--b tone-dusk" role="img" aria-label="Pool area of the property at dusk"></div>

  <h2 class="section-title" style="left:26px;top:256px">General information</h2>
  <a class="edit-link"><svg viewBox="0 0 24 24"><path d="M4 20h4L19 9l-4-4L4 16z"/></svg>Property Edit</a>

  <dl class="info-grid">
    <div class="info-item"><dt>Province</dt><dd>British Columbia</dd></div>
    <div class="info-item"><dt>City</dt><dd>Acton Vale</dd></div>
    <div class="info-item"><dt>Address</dt><dd>240 Harbourline Street, Vancouver, BC</dd></div>
    <div class="info-item"><dt>GPS Address</dt><dd>49.2800000 : -123.1100000000000</dd></div>
    <div class="info-item"><dt>Postal Code</dt><dd>V0X 2K4</dd></div>
    <div class="info-item"><dt>Date Build</dt><dd>07/01/1980</dd></div>
    <div class="info-item"><dt>Area (sq.ft)</dt><dd>1500000.00</dd></div>
    <div class="info-item"><dt>Lot Size</dt><dd>1500000.00</dd></div>
    <div class="info-item"><dt>Zoning</dt><dd>CD1</dd></div>
    <div class="info-item"><dt>Structure type</dt><dd>Steel and concrete</dd></div>
    <div class="info-item"><dt>Building height</dt><dd>250 mt</dd></div>
    <div class="info-item"><dt>Clear height</dt><dd>45 mt</dd></div>
    <div class="info-item"><dt>Floor loading capacity</dt><dd>50</dd></div>
    <div class="info-item"><dt>Number of floors</dt><dd>30</dd></div>
    <div class="info-item"><dt>Number of tenants</dt><dd>30</dd></div>
    <div class="info-item"><dt>Suites</dt><dd>150</dd></div>
    <div class="info-item"><dt>Typical bay size</dt><dd>-</dd></div>
    <div class="info-item"><dt>Building envelope</dt><dd>None</dd></div>
    <div class="info-item"><dt>Parking</dt><dd>Underground + surface</dd></div>
    <div class="info-item"><dt>Parking ration/N. of stalls</dt><dd>6</dd></div>
    <div class="info-item"><dt>Sprinkler protected</dt><dd>Yes</dd></div>
    <div class="info-item"><dt>Sprinkler ESFR</dt><dd>No</dd></div>
    <div class="info-item"><dt>Sprinkler capacity (gpm)</dt><dd>No</dd></div>
    <div class="info-item"><dt>Fire alarm panel</dt><dd>Yes</dd></div>
    <div class="info-item"><dt>Fire alarm monitored</dt><dd>Yes</dd></div>
    <div class="info-item"><dt>Maximum electrical capacity (Amps)</dt><dd>2500</dd></div>
    <div class="info-item"><dt>Building back-up power source</dt><dd>Yes</dd></div>
    <div class="info-item"><dt>Number of elevators</dt><dd>30</dd></div>
    <div class="info-item"><dt>Number of escalators</dt><dd>5</dd></div>
    <div class="info-item"><dt>Roof construction</dt><dd>EPDM</dd></div>
    <div class="info-item"><dt>Roof insulation</dt><dd>-</dd></div>
    <div class="info-item"><dt>Utility meters</dt><dd>-</dd></div>
    <div class="info-item"><dt>Aditional information</dt><dd>-</dd></div>
  </dl>

  <h2 class="section-title" style="left:501px;top:87px;font-size:9.5px">Options</h2>
  <div class="options" style="top:103px">
    <div class="option option--active"><svg viewBox="0 0 24 24"><circle cx="12" cy="12" r="9"/><path d="M12 11v6M12 7v1"/></svg>General information</div>
    <div class="option"><svg viewBox="0 0 24 24"><rect x="9" y="3" width="6" height="5"/><rect x="2" y="16" width="6" height="5"/><rect x="16" y="16" width="6" height="5"/><path d="M12 8v4M5 16v-4h14v4"/></svg>Organization chart</div>
    <div class="option"><svg viewBox="0 0 24 24"><path d="M3 11l9-7 9 7v9H3z"/><circle cx="12" cy="13" r="2"/><path d="M9 19a3 3 0 0 1 6 0"/></svg>Tenant List</div>
    <div class="option"><svg viewBox="0 0 24 24"><path d="M3 11l9-7 9 7v9H3z"/><path d="M12 10v8M14 12h-3a1.5 1.5 0 0 0 0 3h2a1.5 1.5 0 0 1 0 3h-3"/></svg>Property Assets</div>
    <div class="option"><svg viewBox="0 0 24 24"><path d="M5 13h14v7H5zM7 13a5 5 0 0 1 10 0M12 4v4"/></svg>Contractor list</div>
    <div class="option"><svg viewBox="0 0 24 24"><circle cx="12" cy="12" r="3"/><path d="M12 3v4M12 17v4M3 12h4M17 12h4M6 6l3 3M15 15l3 3M18 6l-3 3M9 15l-3 3"/></svg>Compliance mngmt</div>
    <div class="option"><svg viewBox="0 0 24 24"><rect x="5" y="4" width="14" height="17" rx="1"/><path d="M9 4v3h6V4M9 13l2 2 4-4"/></svg>Maint. Work orders</div>
    <div class="option"><svg viewBox="0 0 24 24"><rect x="5" y="4" width="14" height="17" rx="1"/><path d="M9 4v3h6V4M9 17l6-6"/></svg>Work orders</div>
    <div class="option"><svg viewBox="0 0 24 24"><rect x="5" y="3" width="14" height="18" rx="1"/><path d="M12 7v10M14 9h-3a1.5 1.5 0 0 0 0 3h2a1.5 1.5 0 0 1 0 3h-3"/></svg>Purchase orders</div>
    <div class="option"><svg viewBox="0 0 24 24"><path d="M6 3h8l4 4v14H6z"/><path d="M9 12h6M9 16h6"/></svg>Files</div>
  </div>

  <h2 class="section-title" style="left:501px;top:306px;font-size:9.5px">Map Ubication</h2>
  <div class="map" role="img" aria-label="Street map around the property location">
    <div class="map-pin"></div>
    <div class="map-popup">
      <h4>Prime tower</h4>
      <p><svg viewBox="0 0 24 24"><path d="M12 21s7-7 7-12a7 7 0 0 0-14 0c0 5 7 12 7 12z"/><circle cx="12" cy="9" r="2.5"/></svg>240 Harbourline Street, Vancouver, BC</p>
    </div>
    <div class="map-zoom"><span>+</span><span>-</span></div>
  </div>
</section>

</body>
</html>
```